Diverse, up-scale salon needs eye-catching, unique business cards.

We are looking for a unique business card design for our stylist but that can also be multi functional and used for appointment reminder and referrals. I will need a design in a format that I can modify names and titles going forward. In the past we have had a dark background with the logo on one side, and stylist and contact information on the other but we are open to all ideas. I have included our mission statement as well as branded colors below. The statement doesn't need to go on the card, it's just a reference for target market. We need space for the stylists name, title, instagram handle and then the salons phone number, website and address. I am also open to adding a spot for a qr code linked to the stylist instagram or the salon booking link.

primary brand colors:
#333333 #233415 #36502a #93874a #000000
Mission statement:
Vessolin Hair Studio, a high-end salon located in the lively Downtown Farmington, Michigan, is committed to providing exceptional services in a welcoming and relaxed environment to meet the needs of our diverse clientele.
Our salon specializes in contemporary custom haircuts, coloring, extensions, and barbering and beard grooming services. Our team of skilled stylists is passionate and inventive in their hair styling techniques. At the heart of our salon are values centered on quality, innovation, creativity, and above all, comfort. These core values are evident in every appointment across our customizable array of services.
Our goal is to establish a benchmark for exceptional hair care for every human.
Website: www.vessolinhairstudio.example
instagram: @vessolinhairstudio
address: 41782 Pelham Crest Rd, Larkmoor ST
phone: 555-613-4087

Industry/Entity Type

Hair Salon

Contact Information for Business Card

Stylist name, title, phone, instagram, website, address, (optional qr code)

Requirements
Should not have
• Does not need mission statement on the card.

```html
<!DOCTYPE html>
<html lang="en">
<head>
<meta charset="utf-8">
<title>Vessolin Hair Studio — Business Cards</title>
<link rel="stylesheet" href="https://fonts.googleapis.com/css2?family=Montserrat:wght@400;600&display=swap">
<style>
  :root {
    --stage: #3a3a3a;
    --olive: #93874a;
    --charcoal: #333333;
    --ink: #1f1f1f;
    --paper: #ffffff;
  }
  * { margin: 0; padding: 0; box-sizing: border-box; }
  html, body { width: 1200px; height: 769px; overflow: hidden; background: var(--stage); }
  .canvas {
    position: relative; width: 1200px; height: 769px;
    font-family: 'Montserrat', Arial, sans-serif;
  }
  .card {
    position: absolute; top: 240px; width: 500px; height: 286px;
    overflow: hidden; box-shadow: 0 18px 40px rgba(0,0,0,.35);
  }
  .card--front { left: 60px; background: var(--olive); }
  .card--back { left: 640px; background: var(--charcoal); }
  .front-shape { position: absolute; inset: 0; width: 100%; height: 100%; }
  .contact {
    position: absolute; left: 26px; top: 34px; color: var(--paper);
    font-size: 11.5px; line-height: 1.5; list-style: none;
  }
  .contact__address { margin-bottom: 6px; }
  .contact__item { display: flex; align-items: center; gap: 7px; }
  .contact__icon {
    width: 11px; height: 11px; border-radius: 50%; background: var(--paper);
    flex: none;
  }
  .wordmark {
    position: absolute; text-align: center; font-weight: 600;
    letter-spacing: .12em; text-transform: uppercase; line-height: 1.35;
  }
  .wordmark--front {
    left: 300px; top: 112px; width: 180px; font-size: 15px; color: var(--olive);
  }
  .wordmark--back {
    left: 0; right: 0; top: 118px; font-size: 19px; color: var(--paper);
  }
</style>
</head>
<body>
<main class="canvas">
  <section class="card card--front" aria-label="Business card front">
    <svg class="front-shape" viewBox="0 0 500 286" aria-hidden="true">
      <path d="M318 0 Q238 40 236 286 L500 286 L500 0 Z" fill="var(--paper)"/>
      <path d="M336 12 Q268 48 262 286 L252 286 Q256 56 336 12 Z" fill="var(--ink)"/>
    </svg>
    <ul class="contact">
      <li class="contact__address">41782 Pelham Crest Rd,<br>Larkmoor ST</li>
      <li class="contact__item"><span class="contact__icon"></span>555-613-4087</li>
      <li class="contact__item"><span class="contact__icon"></span>www.vessolinhairstudio.example</li>
      <li class="contact__item"><span class="contact__icon"></span>@vessolinhairstudio</li>
    </ul>
    <p class="wordmark wordmark--front">Vessolin<br>Hair Studio</p>
  </section>

  <section class="card card--back" aria-label="Business card back">
    <p class="wordmark wordmark--back">Vessolin<br>Hair Studio</p>
  </section>
</main>
</body>
</html>
```